HVAC Parts Distributor Website

We are working with an HVAC parts distributor to Arcwell a website. They primarily work with HVAC contractors.
They are similar to: https://www.corvelparts.example, and https://www.ductmart.example
Thank you for taking the time to consider designing a website for us. We are web developers based in Stockton, CA, USA. Most of our projects go through the same process. Understanding this process may help you win a project with us. We custom-code all of our websites in-house. We don’t have any requirements as to what tools you use for your Arcwell, but we ask that you follow these guidelines.
IMAGES:
If you use any images or icons in the Arcwell, we ask that you have a link to the asset so we can purchase the image/icon. Most of the designs we submit do not have the customer’s images on them unless they have some great images. Be creative; show us the feeling you are trying to portray with your image choices. Use any royalty-free site you choose. We subscribe to Quillon and mainly use their images, but we can purchase images outside of Quillon.
FONTS:
We ask that you identify the fonts you’re using in the Arcwell. This can be done in a message if you want. We typically use Brevix Fonts and Quillon Fonts.
CONTENT:
We're always open to different content and ideas. We often submit designs with stock images so the client can see our vision. We typically take pictures after the website launch to use their images with our vision. Lorem Ipsum is fine for paragraphs, but we ask that you make the Headers with correct English. We want to be able to show the vision and identify the sections of the website.
INSPIRATION:
We typically add a couple of links in the brief of websites we like to help you get started in your Arcwell.
REVISIONS:
We do not often ask for revisions of the designs unless we see something in the Arcwell that may not appeal to the client. If there are slight changes that we want to make, we simply do that in the development process.
FEEDBACK:
We rarely give feedback on designs during the Arcwell process. We are working on many website projects and do not have the time to give feedback. We usually respond if your request is well thought out and asks specific questions, but a note asking “feedback, please” usually goes unanswered.

```html
<!DOCTYPE html>
<html lang="en">
<head>
<meta charset="utf-8">
<title>Kestrel HVAC Supply</title>
<link href="https://fonts.googleapis.com/css2?family=Roboto:wght@400;500;700&display=swap" rel="stylesheet">
<style>
:root{--green:#8ea80e;--green-light:#f3f7df;--dark:#222;--text:#222;--muted:#666;--panel:#efefef;--sky:#8dd2f0;--kraft:#c9a878;--steel:#5a6f94}
*{box-sizing:border-box;margin:0;padding:0}
html,body{width:1200px;height:2953px;overflow:hidden}
body{font-family:Roboto,sans-serif;color:var(--text);background:#fff;position:relative}
.abs{position:absolute}
.header{top:0;left:0;width:1200px;height:89px}
.brand{left:111px;top:25px;display:flex;align-items:center;gap:12px;font-weight:700;font-size:30px;color:var(--dark)}
.brand i{width:34px;height:34px;background:var(--green);display:block}
.search{left:468px;top:23px;width:406px;height:43px;border:1px solid #ddd;border-radius:22px;background:#f3f3f3;font-size:16px;color:#666;padding:12px 0 0 25px}
.search span{position:absolute;right:7px;top:6px;width:30px;height:30px;border-radius:50%;background:var(--green)}
.account{top:35px;font-size:16px;color:#666}
.nav{top:89px;left:0;width:1200px;height:45px;background:var(--dark);display:flex;padding-left:119px}
.nav a{color:#fff;font-size:14px;font-weight:500;text-decoration:none;padding:0 18.5px;line-height:45px}
.nav a.active{background:var(--green)}
.hero{top:134px;left:0;width:1200px;height:642px;color:#fff;text-align:center;overflow:hidden;
 background:
  radial-gradient(ellipse 300px 190px at 600px 430px,#b8946a 0%,#a98560 55%,rgba(169,133,96,0) 100%),
  radial-gradient(ellipse 720px 170px at 640px 600px,#3e5478 0%,#63789a 45%,rgba(120,135,160,0) 100%),
  radial-gradient(ellipse 260px 160px at 200px 200px,rgba(190,165,125,.85),rgba(190,165,125,0)),
  radial-gradient(ellipse 300px 260px at 1050px 250px,rgba(200,175,135,.8),rgba(200,175,135,0)),
  linear-gradient(180deg,#8e8f90 0%,#b7b1a6 45%,#cfc8bb 70%,#a89c8a 100%)}
.hero::before{content:"";position:absolute;inset:0;background:linear-gradient(180deg,rgba(0,0,0,.28) 0%,rgba(0,0,0,.08) 45%,rgba(0,0,0,0) 60%)}
.hero h1{position:absolute;top:55px;width:100%;font-size:55px;font-weight:700}
.hero p{position:absolute;top:125px;left:330px;width:540px;font-size:15px;line-height:26px}
.btn{display:inline-block;background:var(--green);color:#fff;font-weight:700;font-size:14px}
.hero .btn{position:absolute;top:195px;left:534px;width:132px;height:38px;line-height:38px}
.round{width:44px;height:44px;border-radius:50%;background:#eee;display:flex;align-items:center;justify-content:center}
.dots{top:564px;left:563px;display:flex;gap:8px}
.dots b{width:12px;height:12px;border:2px solid #fff;border-radius:50%}
.dots b.on{background:#fff}
.cats{top:785px;left:9px;display:flex;gap:17px}
.cat{width:133px;height:128px;background:var(--green-light);text-align:center;font-size:15px;font-weight:700;padding-top:24px}
.cat svg{display:block;margin:0 auto 12px}
h2{font-size:41px;font-weight:700;text-align:center;position:absolute;width:1200px;left:0}
.photo{top:1077px;height:277px;width:229px}
.quote{top:1077px;height:277px;width:229px;background:var(--panel);text-align:center;padding:26px 24px}
.quote h3{font-size:19px;font-weight:500;margin-bottom:14px}
.quote p{font-size:14px;color:var(--muted);line-height:26px}
.features{top:1364px;left:0;width:1200px;height:825px;background:
  radial-gradient(ellipse 260px 220px at 160px 420px,rgba(226,210,185,.55),rgba(226,210,185,0)),
  radial-gradient(ellipse 280px 240px at 1030px 300px,rgba(226,210,185,.5),rgba(226,210,185,0)),
  linear-gradient(180deg,#fff 0%,#f7f4ef 40%,#f1ebe2 100%)}
.ring{left:421px;top:1644px;width:356px;height:356px;border-radius:50%;background:#d6d9dc;padding:8px}
.ring div{width:100%;height:100%;border-radius:50%;background:
  radial-gradient(ellipse 70px 55px at 110px 150px,#d1ad7c,rgba(209,173,124,0) 100%),
  radial-gradient(ellipse 85px 60px at 120px 225px,#c89f6c,rgba(200,159,108,0) 100%),
  radial-gradient(ellipse 75px 55px at 230px 215px,#d4b282,rgba(212,178,130,0) 100%),
  radial-gradient(circle at 50% 45%,#9bd8f3 0%,var(--sky) 70%,#7cc6e8 100%)}
.ficon{width:80px;height:80px;border-radius:50%;background:#fff;border:2px solid #ddd;display:flex;align-items:center;justify-content:center;box-shadow:0 2px 6px rgba(0,0,0,.15)}
.flabel{font-size:16px;font-weight:500}
.brands{top:2189px;left:0;width:1200px;height:357px;background:var(--green)}
.logo{top:2351px;width:178px;height:91px;background:#fff;display:flex;align-items:center;justify-content:center;gap:8px;font-size:18px;font-weight:500;color:#444}
.logo i{width:20px;height:20px;border-radius:50%;background:#9aa;display:block}
.fcol h4{font-size:21px;font-weight:500;margin-bottom:18px}
.fcol a{display:block;font-size:14px;color:#666;text-decoration:none;line-height:26px}
.email{left:808px;top:2700px;width:281px;height:42px;border:1px solid #ccc;font-size:13px;color:#666;padding:13px 18px}
.sub{left:808px;top:2754px;width:109px;height:41px;line-height:41px;text-align:center;font-size:13px}
.copy{top:2876px;width:1200px;text-align:center;font-size:14px;color:#444}
</style>
</head>
<body>
<header class="header abs">
  <div class="brand abs"><i></i>Kestrel HVAC Supply</div>
  <div class="search abs">Search for a product<span></span></div>
  <div class="account abs" style="left:905px">Sign in</div>
  <div class="account abs" style="left:991px">Cart : $0.00</div>
</header>
<nav class="nav abs">
  <a class="active">Home</a><a>Plumbing</a><a>Heating</a><a>HVAC</a><a>PEX</a><a>Fittings</a><a>Valves</a><a>Thermostats</a><a>Electrical</a><a>Resources</a><a>Our Team</a>
</nav>
<section class="hero abs" role="img" aria-label="Shipping box riding a curved roller conveyor in a warehouse">
  <h1>Kestrel HVAC Supply</h1>
  <p>Lorem ipsum dolor sit amet, consectetur adipiscing elit, sed do eiusmod tempor incididunt ut labore et dolore magna aliqua.</p>
  <span class="btn">GET A QUOTE</span>
  <div class="round abs" style="left:67px;top:315px"><svg width="14" height="14" viewBox="0 0 14 14"><path d="M9 2 4 7l5 5" fill="none" stroke="#333" stroke-width="2"/></svg></div>
  <div class="round abs" style="left:1087px;top:315px"><svg width="14" height="14" viewBox="0 0 14 14"><path d="m5 2 5 5-5 5" fill="none" stroke="#333" stroke-width="2"/></svg></div>
  <div class="dots abs"><b></b><b></b><b class="on"></b><b></b></div>
</section>
<div class="cats abs">
  <div class="cat"><svg width="46" height="46" viewBox="0 0 46 46" fill="#8ea80e"><rect x="4" y="6" width="30" height="12"/><rect x="16" y="18" width="8" height="24"/></svg>Plumbing</div>
  <div class="cat"><svg width="46" height="46" viewBox="0 0 46 46" fill="none" stroke="#8ea80e" stroke-width="5"><path d="M10 4c-6 10 6 14 0 38M23 4c-6 10 6 14 0 38M36 4c-6 10 6 14 0 38"/></svg>Heating</div>
  <div class="cat"><svg width="46" height="46" viewBox="0 0 46 46" fill="none" stroke="#8ea80e" stroke-width="7"><path d="M8 4v14h20v24"/></svg>HVAC</div>
  <div class="cat"><svg width="46" height="46" viewBox="0 0 46 46" fill="none" stroke="#8ea80e" stroke-width="6"><path d="M8 8h22a8 8 0 0 1 0 16H16a8 8 0 0 0 0 16h22"/></svg>PEX</div>
  <div class="cat"><svg width="46" height="46" viewBox="0 0 46 46" fill="#8ea80e"><rect x="2" y="2" width="19" height="19" rx="4"/><rect x="25" y="2" width="19" height="19" rx="4"/><rect x="2" y="25" width="19" height="19" rx="4"/><rect x="25" y="25" width="19" height="19" rx="4"/></svg>Fittings</div>
  <div class="cat"><svg width="46" height="46" viewBox="0 0 46 46" fill="#8ea80e"><rect x="12" y="4" width="22" height="6"/><rect x="20" y="10" width="6" height="10"/><rect x="2" y="24" width="42" height="16"/></svg>Valves</div>
  <div class="cat"><svg width="46" height="46" viewBox="0 0 46 46" fill="none" stroke="#8ea80e" stroke-width="6"><path d="M6 6l34 34M40 6 6 40"/></svg>Tools</div>
  <div class="cat"><svg width="46" height="46" viewBox="0 0 46 46"><circle cx="23" cy="23" r="20" fill="none" stroke="#8ea80e" stroke-width="4"/><path d="M26 6 14 26h9l-3 14 12-20h-9z" fill="#8ea80e"/></svg>Electrical</div>
</div>

<h2 style="top:1006px">Customers Say...</h2>
<svg class="abs" style="left:44px;top:1192px" width="20" height="24" viewBox="0 0 20 24"><path d="M14 2 4 12l10 10" fill="none" stroke="#222" stroke-width="3"/></svg>
<svg class="abs" style="left:1134px;top:1192px" width="20" height="24" viewBox="0 0 20 24"><path d="m6 2 10 10-10 10" fill="none" stroke="#222" stroke-width="3"/></svg>
<div class="photo abs" style="left:111px;background:linear-gradient(160deg,#f4f1ec,#d9b27a)" role="img" aria-label="Customer holding stacked boxes"></div>
<div class="quote abs" style="left:356px"><h3>Duis aute irure</h3><p>Lorem ipsum dolor sit amet, consectetur adipiscing elit, sed do eiusmod tempor incididunt ut labore et dolore magna aliqua. Ut enim ad minim veniam, quis nostrud exercitation ullamco</p></div>
<div class="photo abs" style="left:614px;background:linear-gradient(160deg,#f2f2f2,#9bb8e0)" role="img" aria-label="Delivery worker with box and clipboard"></div>
<div class="quote abs" style="left:860px"><h3>Duis aute irure</h3><p>Lorem ipsum dolor sit amet, consectetur adipiscing elit, sed do eiusmod tempor incididunt ut labore et dolore magna aliqua. Ut enim ad minim veniam, quis nostrud exercitation ullamco</p></div>

<section class="features abs" role="img" aria-label="Faded background of stacked moving boxes"></section>
<h2 style="top:1446px">Our Features</h2>
<div class="ring abs"><div role="img" aria-label="Cardboard shipping boxes on a sky blue background"></div></div>
<div class="ficon abs" style="left:557px;top:1519px"><svg width="40" height="28" viewBox="0 0 40 28" fill="#8ea80e"><rect x="4" y="4" width="22" height="16"/><path d="M26 9h8l5 6v5H26z"/><circle cx="11" cy="23" r="4"/><circle cx="32" cy="23" r="4"/></svg></div>
<div class="flabel abs" style="left:500px;top:1603px;width:195px;text-align:center">Free Shipping</div>
<div class="ficon abs" style="left:361px;top:1637px"><svg width="36" height="36" viewBox="0 0 36 36" fill="#8ea80e"><path d="M18 2 32 7v10c0 9-6 14-14 17C10 31 4 26 4 17V7z"/></svg></div>
<div class="flabel abs" style="left:260px;top:1666px;width:88px;text-align:right">Trust</div>
<div class="ficon abs" style="left:752px;top:1637px"><svg width="36" height="36" viewBox="0 0 36 36" fill="#8ea80e"><path d="M5 8h7v12h5l-8.5 10L0 20h5zM24 8h7v12h5l-8.5 10L19 20h5z"/></svg></div>
<div class="flabel abs" style="left:856px;top:1666px">Lower Prices</div>
<div class="ficon abs" style="left:352px;top:1894px"><svg width="36" height="36" viewBox="0 0 36 36" fill="#8ea80e"><path d="M8 3l6 6-4 5c2 5 6 9 11 11l5-4 6 6-5 6C14 33 3 22 2 8z"/></svg></div>
<div class="flabel abs" style="left:220px;top:1912px;width:120px;text-align:right;line-height:21px">Desicated<br>Phone Line</div>
<div class="ficon abs" style="left:772px;top:1894px"><svg width="36" height="36" viewBox="0 0 36 36" fill="#8ea80e"><rect x="4" y="4" width="24" height="22"/><path d="M22 30a8 8 0 1 0 0-10" fill="none" stroke="#8ea80e" stroke-width="3"/></svg></div>
<div class="flabel abs" style="left:864px;top:1923px">Free Returns</div>
<div class="ficon abs" style="left:557px;top:2011px"><svg width="38" height="38" viewBox="0 0 38 38"><circle cx="19" cy="19" r="13" fill="none" stroke="#8ea80e" stroke-width="6" stroke-dasharray="5 3"/><circle cx="19" cy="19" r="6" fill="#8ea80e"/></svg></div>
<div class="flabel abs" style="left:500px;top:2095px;width:195px;text-align:center">Exclusive Gear</div>

<section class="brands abs"></section>
<h2 style="top:2270px;color:#fff">Trusted Brands</h2>
<div class="logo abs" style="left:111px"><i></i>Lumen</div>
<div class="logo abs" style="left:311px"><i></i>Arcwell</div>
<div class="logo abs" style="left:511px"><i></i>Novara</div>
<div class="logo abs" style="left:711px"><i></i>Tessel</div>
<div class="logo abs" style="left:910px"><i></i>Brightloop</div>

<div class="fcol abs" style="left:111px;top:2646px"><h4>Customer Services</h4><a>Order Status</a><a>Contact Us</a><a>Shipping Policy</a><a>Returns</a><a>FAQs</a></div>
<div class="fcol abs" style="left:351px;top:2646px"><h4>About Us</h4><a>Meet The Team</a><a>Careers</a><a>Our Blog</a></div>
<div class="fcol abs" style="left:557px;top:2646px"><h4>Resources &amp; Tools</h4><a>Reorder</a><a>Quick Order</a><a>Saved Carts</a><a>Project Calculators</a><a>Video Library</a></div>
<div class="fcol abs" style="left:808px;top:2646px"><h4>SUBSCRIBE FOR MORE</h4></div>
<div class="email abs">Email address</div>
<span class="btn sub abs">SUBSCRIBE</span>
<div class="copy abs">© Copyrights 2023 Company name | All Rights Reserved</div>
</body>
</html>
```